Private Investment Firm Needs PowerPoint Presentation Template

Design PowerPoint template, take Pinebrook-submitted rough presentation draft, and drop it into new template. See attached Project Brief file for more detail.
Updates

Some decent designs have been submitted but they seem to lack the understanding of our target markets. I am hopeful that more time and feedback will result in better results.

Target Market(s)

Private company owners and intermediaries.

Font styles to use
Serif

Colors
3176b5

Requirements
Must have
• See attached Project Brief.
Nice to have
Should not have
• No B2C fluff--this is a B2B project.

```html
<!DOCTYPE html>
<html lang="en">
<head>
<meta charset="utf-8">
<title>Pinebrook Capital – Presentation Template</title>
<link rel="stylesheet" href="https://fonts.googleapis.com/css2?family=Cinzel:wght@500;600&family=Montserrat:wght@400;500;600;700&display=swap">
<style>
  :root {
    --brand-blue: #1b6fc1;
    --brand-blue-deep: #1565b5;
    --brand-blue-light: #2b8ad8;
    --ink-gray: #4a4a4a;
    --body-gray: #555;
    --band-gray: #6d6d6d;
    --paper: #ffffff;
    --paper-shade: #f1f2f4;
    --backdrop: #e4e4e4;
  }
  * { box-sizing: border-box; margin: 0; padding: 0; }
  html, body { width: 1200px; height: 1160px; overflow: hidden; }
  body {
    background: var(--backdrop);
    font-family: "Montserrat", Arial, sans-serif;
    position: relative;
  }
  .slide {
    position: absolute;
    background: linear-gradient(120deg, var(--paper) 40%, var(--paper-shade));
    box-shadow: 0 4px 14px rgba(0,0,0,0.22);
    overflow: hidden;
  }
  .slide svg.shapes { position: absolute; inset: 0; }

  /* Title slide */
  .slide--title { left: 178px; top: 62px; width: 886px; height: 496px; }
  .title-heading {
    position: absolute; left: 40px; width: 480px; top: 110px;
    text-align: center;
    font-family: "Cinzel", Georgia, serif; font-weight: 500;
    font-size: 35px; line-height: 40px; color: var(--brand-blue);
  }
  .title-sub {
    position: absolute; left: 40px; width: 480px; top: 236px;
    text-align: center; font-size: 13.5px; line-height: 19px; color: var(--body-gray);
  }
  .title-sub strong { color: var(--brand-blue); font-weight: 700; }

  .brand {
    position: absolute; display: flex; align-items: center; justify-content: center; gap: 8px;
    font-family: "Cinzel", Georgia, serif; font-weight: 600; color: var(--brand-blue-deep);
    letter-spacing: 1px;
  }
  .brand-dot { border-radius: 50%; background: var(--brand-blue-deep); }
  .slide--title .brand { left: 40px; width: 480px; top: 350px; font-size: 19px; }
  .slide--title .brand-dot { width: 26px; height: 26px; }

  .web { position: absolute; text-align: center; color: #333; }
  .web b { color: var(--brand-blue); font-weight: 600; }
  .slide--title .web { left: 40px; width: 480px; top: 407px; font-size: 19.5px; }

  /* Introduction slide */
  .slide--intro { left: 181px; top: 586px; width: 879px; height: 494px; }
  .intro-heading {
    position: absolute; left: 0; width: 800px; top: 44px; text-align: center;
    font-weight: 700; font-size: 30px; letter-spacing: 1px; color: var(--brand-blue-deep);
  }
  .intro-rule {
    position: absolute; left: 428px; top: 82px; width: 44px; height: 4px; background: var(--brand-blue-deep);
  }
  .intro-lead {
    position: absolute; left: 100px; width: 700px; top: 110px; text-align: center;
    font-size: 28px; line-height: 31px; color: var(--ink-gray);
  }
  .intro-point {
    position: absolute; width: 280px; font-size: 12px; line-height: 13.5px;
    color: var(--body-gray); text-align: justify;
  }
  .intro-point p + p { margin-top: 12px; }
  .intro-point .bullet { color: var(--brand-blue); }
  .slide--intro .brand { left: 100px; width: 700px; top: 406px; font-size: 15px; }
  .slide--intro .brand-dot { width: 20px; height: 20px; }
  .slide--intro .web { left: 100px; width: 700px; top: 449px; font-size: 15px; }
</style>
</head>
<body>

<section class="slide slide--title">
  <svg class="shapes" width="886" height="496" viewBox="0 0 886 496">
    <defs>
      <linearGradient id="cityTone" x1="0" y1="0" x2="0" y2="1">
        <stop offset="0" stop-color="#5c84b5"/>
        <stop offset="0.35" stop-color="#6a7690"/>
        <stop offset="0.7" stop-color="#5a4a42"/>
        <stop offset="1" stop-color="#3a3630"/>
      </linearGradient>
    </defs>
    <polygon class="accent-band" points="0,0 88,0 0,368" fill="var(--brand-blue)"/>
    <polygon class="city-photo" role="img" aria-label="Photo of a lit city skyline with tall office towers and a busy avenue at dusk"
      points="562,0 886,0 886,496 406,496" fill="url(#cityTone)"/>
  </svg>
  <h1 class="title-heading">Introduction to<br>Non-Control Capital</h1>
  <p class="title-sub">The Lower Middle Market Private Company Strategy for<br>Raising Capital While <strong>Maintaining Business Control</strong></p>
  <div class="brand"><span class="brand-dot"></span>Pinebrook Capital</div>
  <p class="web">www.<b>pinebrookcapital</b>.com</p>
</section>

<section class="slide slide--intro">
  <svg class="shapes" width="879" height="494" viewBox="0 0 879 494">
    <polygon class="accent-band" points="0,0 88,0 0,470" fill="var(--band-gray)"/>
    <polygon class="accent-arrow" points="766,0 879,0 879,494 763,494 842,242" fill="var(--brand-blue-deep)"/>
    <polygon points="842,242 879,160 879,494 800,494" fill="var(--brand-blue-light)" opacity="0.45"/>
  </svg>
  <h2 class="intro-heading">INTRODUCTION</h2>
  <div class="intro-rule"></div>
  <p class="intro-lead">Private company owners have traditionally<br>considered two capital raising options</p>

  <div class="intro-point" style="left:138px; top:218px;">
    <p><span class="bullet">•</span> Borrow from a local bank, or</p>
    <p><span class="bullet">•</span> Sell most or all of the company to a change-of-control investor (aka Buyout firm)</p>
  </div>
  <div class="intro-point" style="left:474px; top:218px;">
    <p><span class="bullet">•</span> Non-Control Capital is not appropriate for every private company owner but neither is a Change-of-Control sale</p>
  </div>
  <div class="intro-point" style="left:138px; top:304px;">
    <p><span class="bullet">•</span> An alternative most have not considered is the raising of Non-Control Capital, or capital that is invested into the business yet allows those same owners to retain controlling interest in their company</p>
  </div>
  <div class="intro-point" style="left:474px; top:304px;">
    <p><span class="bullet">•</span> The key is to determine what the business and owners require, and then partner with an investor best aligned with those needs so that long-term company growth, and personal goals, can both be achieved</p>
  </div>

  <div class="brand"><span class="brand-dot"></span>Pinebrook Capital</div>
  <p class="web">www.<b>pinebrookcapital</b>.com</p>
</section>

</body>
</html>
```